Bramwell Crest Electric van design

Looking to design a wrap for a 2021 varenta cargolux high roof using orange black and dark grey colors like in the logo

```html
<!DOCTYPE html>
<html lang="en">
<head>
<meta charset="utf-8">
<title>Bramwell Crest Electric – Van Wrap</title>
<link href="https://fonts.googleapis.com/css2?family=Montserrat:wght@600&display=swap" rel="stylesheet">
<style>
  :root {
    --backdrop: #ececec;
    --wrap-red: #e2463a;
    --wrap-red-deep: #c8342a;
    --wrap-black: #1e1e1e;
    --trim-grey: #2b2b2b;
    --glass: #9ea8aa;
    --hub: #b9bcbe;
    --type-white: #f4f4f4;
  }
  html, body {
    margin: 0;
    padding: 0;
    width: 1200px;
    height: 800px;
    overflow: hidden;
    background: var(--backdrop);
  }
  .wrap-canvas {
    display: block;
    width: 1200px;
    height: 800px;
  }
  .body-black { fill: var(--wrap-black); }
  .wrap-red { fill: var(--wrap-red); }
  .rub-strip { fill: var(--trim-grey); }
  .skirt-red { fill: var(--wrap-red-deep); }
  .panel-line { fill: none; stroke: #000; stroke-opacity: .35; stroke-width: 3; }
  .glass { fill: var(--glass); }
  .handle { fill: #111; }
  .tire { fill: #161616; }
  .hub { fill: var(--hub); }
  .hub-center { fill: #555; }
  .brand-dot { fill: var(--type-white); }
  .brand-name {
    font-family: "Montserrat", sans-serif;
    font-weight: 600;
    font-size: 60px;
    fill: var(--type-white);
  }
  .tail-light { fill: #b51f22; }
  .tail-lens { fill: #e9e9e9; }
</style>
</head>
<body>
<svg class="wrap-canvas" viewBox="0 0 2250 1500" xmlns="http://www.w3.org/2000/svg">
  <defs>
    <clipPath id="van-shape">
      <path d="M255,1095 L255,450 Q258,415 330,413 L1300,418 Q1420,430 1545,550 L1725,750 Q1965,800 1985,860 L1992,1060 L1992,1095 Z"/>
    </clipPath>
  </defs>

  <g class="van-side">
    <path class="body-black" d="M255,1095 L255,450 Q258,415 330,413 L1300,418 Q1420,430 1545,550 L1725,750 Q1965,800 1985,860 L1992,1060 L1992,1095 Z"/>

    <g clip-path="url(#van-shape)">
      <polygon class="wrap-red" points="200,413 520,413 915,1118 200,1118"/>
      <rect class="rub-strip" x="250" y="965" width="1750" height="60"/>
      <polygon class="skirt-red" points="250,1025 857,1025 910,1118 250,1118"/>
    </g>

    <path class="panel-line" d="M318,540 L1310,540 L1330,545"/>
    <path class="panel-line" d="M1315,420 L1315,965"/>
    <path class="panel-line" d="M1350,540 L1360,1025"/>
    <path class="panel-line" d="M1665,780 L1668,960"/>
    <rect class="panel-line" x="345" y="558" width="935" height="228" rx="28"/>

    <path class="glass" d="M1360,570 L1515,575 L1535,770 L1360,755 Q1352,660 1360,570 Z"/>
    <path class="glass" d="M1533,605 L1620,690 L1622,785 L1545,772 Z"/>

    <rect class="handle" x="1222" y="816" width="80" height="12" rx="6"/>
    <rect class="handle" x="1355" y="816" width="80" height="12" rx="6"/>

    <rect class="tail-light" x="255" y="785" width="44" height="175"/>
    <rect class="tail-lens" x="255" y="835" width="44" height="35"/>
    <rect class="tail-lens" x="255" y="905" width="44" height="14"/>
    <rect class="tail-lens" x="255" y="927" width="44" height="14"/>

    <g class="wheel rear-wheel">
      <circle class="tire" cx="617" cy="1078" r="104"/>
      <circle class="hub" cx="617" cy="1078" r="72"/>
      <circle class="hub-center" cx="617" cy="1078" r="22"/>
    </g>
    <g class="wheel front-wheel">
      <circle class="tire" cx="1738" cy="1078" r="104"/>
      <circle class="hub" cx="1738" cy="1078" r="72"/>
      <circle class="hub-center" cx="1738" cy="1078" r="22"/>
    </g>
  </g>

  <g class="brand-lockup">
    <circle class="brand-dot" cx="680" cy="665" r="70"/>
    <text class="brand-name" x="775" y="650">Bramwell Crest</text>
    <text class="brand-name" x="775" y="722">Electric</text>
  </g>
</svg>
</body>
</html>
```